Business card for Eyelash extension salon in Beverly Hills,California USA

We need new business card for our salon in Beverly Hills. The salon name is 'Lashvera' . We would like to have...Business name: Lashvera Name of person: will provide later Address 4720 N.Alder Crest Ave Marlowe Heights , ST 00417 Phone: will provide later (Text only) Web: www.lashverastudio.example Snapgrid icon, Circlebook icon follow us for seasonal campaign and news @lashverastudiolounge Design should look elegant, high-end, clean, simple, cohesive with my brand. Please refer my brand board. Business name color will be metallic bronzy color. Im thinking grey background or white background. Thanks

Target Market(s)

25-35. Gender neutral. People who are in Entertainment business industry.
This is High-end Eyelash extension salon in Beverly Hills

Industry/Entity Type

Beauty Salon

Contact Information for Business Card

Business name: Lashvera
Name of person: will provide later
Address 4720 N.Alder Crest Ave Marlowe Heights , ST 00417
Phone: will provide later (Text only)
Web: www.lashverastudio.example
Snapgrid icon, Circlebook icon
follow us for seasonal campaign and news @lashverastudiolounge

Requirements
Must have
• Beautiful, elegant, clean and simple look but very attractive and modern
Should not have
• We don't like too clutter, too busy designs.

```html
<!DOCTYPE html>
<html lang="en">
<head>
<meta charset="utf-8">
<title>Lashvera Business Card</title>
<link rel="stylesheet" href="https://fonts.googleapis.com/css2?family=Cormorant+Garamond:wght@500;600&family=Playfair+Display:wght@500&display=swap">
<style>
  :root {
    --backdrop: #dcdcdc;
    --card-white: #ffffff;
    --bronze: #8a6a53;
    --bronze-ink: #7d5c48;
    --rule: #9a7e6c;
    --on-bronze: #ffffff;
  }
  html, body {
    margin: 0;
    padding: 0;
    width: 1200px;
    height: 930px;
    overflow: hidden;
    background: var(--backdrop);
  }
  .canvas {
    position: relative;
    width: 1200px;
    height: 930px;
  }
  .card {
    position: absolute;
    left: 318px;
    width: 564px;
    height: 323px;
    box-shadow: 0 4px 10px rgba(0, 0, 0, 0.28);
  }
  .card--front { top: 125px; background: var(--card-white); }
  .card--back { top: 514px; background: var(--bronze); }

  .rule { position: absolute; background: var(--rule); }
  .rule--top { left: 36px; top: 38px; width: 287px; height: 1px; }
  .rule--side { left: 36px; top: 38px; width: 1px; height: 86px; }
  .rule--bottom { left: 80px; top: 289px; width: 243px; height: 1px; }

  .holder {
    position: absolute;
    bottom: 32px;
    writing-mode: vertical-rl;
    transform: rotate(180deg);
    color: var(--bronze-ink);
    white-space: nowrap;
  }
  .holder__name {
    left: 29px;
    font-family: "Playfair Display", serif;
    font-weight: 500;
    font-size: 17px;
    letter-spacing: 0.3px;
  }
  .holder__role {
    left: 54px;
    font-family: "Cormorant Garamond", serif;
    font-weight: 500;
    font-size: 14px;
    letter-spacing: 0.6px;
  }

  .contact {
    position: absolute;
    left: 335px;
    margin: 0;
    font-family: "Cormorant Garamond", serif;
    font-weight: 500;
    font-size: 15px;
    font-variant-numeric: lining-nums;
    letter-spacing: 0.9px;
    line-height: 25px;
    color: var(--bronze-ink);
    white-space: nowrap;
  }
  .contact--web { top: 26px; }
  .contact--direct { top: 134px; }
  .contact--address { top: 246px; }

  .brand {
    position: absolute;
    inset: 0;
    display: flex;
    align-items: center;
    justify-content: center;
    font-family: "Cormorant Garamond", serif;
    font-weight: 500;
    font-size: 60px;
    letter-spacing: 2px;
    color: var(--on-bronze);
    margin: 0;
  }
</style>
</head>
<body>
<main class="canvas">
  <section class="card card--front" aria-label="Card front">
    <span class="rule rule--top"></span>
    <span class="rule rule--side"></span>
    <span class="rule rule--bottom"></span>
    <span class="holder holder__name">CLARA J. BENTON</span>
    <span class="holder holder__role">Director</span>
    <p class="contact contact--web">www.lashverastudio.example</p>
    <p class="contact contact--direct">555.014.0184<br>hello@lashverastudio.example</p>
    <p class="contact contact--address">4720 N.Alder Crest Ave<br>Marlowe Heights , ST 00417</p>
  </section>
  <section class="card card--back" aria-label="Card back">
    <h1 class="brand">Lashvera</h1>
  </section>
</main>
</body>
</html>
```